Dalvick's Business Card

I need some designs for a new business card including the new logo attached. An old example of our business card is also attached to show all the data that should be included on the new design.
**I added some more examples someone had mocked up**

Contact Information for Business Card

Should include all info on other examples uploaded.

```html
<!DOCTYPE html>
<html lang="en">
<head>
<meta charset="utf-8">
<title>Dalvick's Business Card</title>
<link href="https://fonts.googleapis.com/css2?family=Montserrat:wght@500;600;700&family=Arimo:wght@400;700&display=swap" rel="stylesheet">
<style>
  :root {
    --bg: #e8e8e8;
    --card-blue: #0b6fc4;
    --brand-red: #ec1c24;
    --white: #ffffff;
  }
  * { box-sizing: border-box; margin: 0; padding: 0; }
  html, body { width: 1200px; height: 802px; overflow: hidden; background: var(--bg); }
  .canvas {
    width: 1200px; height: 802px;
    display: flex; align-items: center; justify-content: center; gap: 40px;
  }
  .card {
    position: relative; width: 560px; height: 320px;
    background: var(--card-blue); color: var(--white); overflow: hidden;
    box-shadow: 0 6px 18px rgba(0,0,0,.18);
  }
  /* Front */
  .corner-band {
    position: absolute; top: 0; right: 0; width: 0; height: 0;
    border-top: 200px solid var(--brand-red); border-left: 200px solid transparent;
  }
  .brand-mark {
    position: absolute; right: 40px; top: 60px; width: 200px; height: 200px;
    border-radius: 50%; background: var(--white); border: 10px solid var(--brand-red);
  }
  .front-info { position: absolute; left: 36px; top: 42px; }
  .wordmark {
    font-family: "Montserrat", sans-serif; font-weight: 700; font-size: 48px;
    letter-spacing: 1px; line-height: 1;
  }
  .tagline {
    font-family: "Montserrat", sans-serif; font-weight: 600; font-size: 10.5px;
    letter-spacing: .4px; margin-top: 4px;
  }
  .person {
    font-family: "Montserrat", sans-serif; font-weight: 700; font-size: 22px; margin-top: 30px;
  }
  .contact { list-style: none; margin-top: 16px; font-family: "Arimo", sans-serif; font-size: 15px; }
  .contact li { display: flex; align-items: center; gap: 8px; margin-bottom: 4px; }
  .contact svg { width: 14px; height: 14px; fill: var(--white); }
  .credentials {
    font-family: "Arimo", sans-serif; font-size: 15px; letter-spacing: .5px;
    margin-top: 18px; line-height: 1.3; text-transform: uppercase;
  }
  /* Back */
  .back-brand {
    position: absolute; top: 80px; left: 0; right: 0;
    display: flex; align-items: center; justify-content: center; gap: 14px;
  }
  .back-mark {
    width: 62px; height: 62px; border-radius: 50%;
    background: var(--white); border: 5px solid var(--brand-red);
  }
  .back-brand .wordmark { font-size: 54px; }
  .back-brand .tagline { color: var(--brand-red); font-size: 11.5px; }
  .service-area {
    position: absolute; top: 196px; left: 50%; transform: translateX(-50%);
    background: var(--brand-red); white-space: nowrap;
    font-family: "Arimo", sans-serif; font-size: 17px; padding: 4px 12px;
  }
  .call-to-action {
    position: absolute; bottom: 30px; left: 0; right: 0; text-align: center;
    font-family: "Arimo", sans-serif; font-weight: 700; font-size: 13.5px; letter-spacing: .3px;
  }
</style>
</head>
<body>
<main class="canvas">
  <section class="card card-front">
    <div class="corner-band"></div>
    <div class="brand-mark"></div>
    <div class="front-info">
      <h1 class="wordmark">DALVICK'S</h1>
      <p class="tagline">AIR CONDITIONING &amp; HEATING SERVICE</p>
      <p class="person">EVAN DALVICK</p>
      <ul class="contact">
        <li><svg viewBox="0 0 24 24"><path d="M6.6 10.8a15.1 15.1 0 0 0 6.6 6.6l2.2-2.2c.3-.3.7-.4 1-.2 1.1.4 2.3.6 3.6.6.6 0 1 .4 1 1V20c0 .6-.4 1-1 1A17 17 0 0 1 3 4c0-.6.4-1 1-1h3.5c.6 0 1 .4 1 1 0 1.3.2 2.5.6 3.6.1.3 0 .7-.2 1z"/></svg>555.014.2287</li>
        <li><svg viewBox="0 0 24 24"><path d="M2 5h20v14H2zm2 2v.5l8 5 8-5V7l-8 5z"/></svg>hvacdalvick@mailbox.com</li>
      </ul>
      <p class="credentials">Licensed &amp; Insured<br>Family Owned &amp; Operated</p>
    </div>
  </section>

  <section class="card card-back">
    <div class="back-brand">
      <div class="back-mark"></div>
      <div>
        <h2 class="wordmark">DALVICK'S</h2>
        <p class="tagline">AIR CONDITIONING &amp; HEATING SERVICE</p>
      </div>
    </div>
    <p class="service-area">Serves Millbrook, IA &amp; Surrounding Areas</p>
    <p class="call-to-action">CALL TODAY FOR ALL YOUR HVAC, REFRIGERATION &amp; PLUMBING NEEDS</p>
  </section>
</main>
</body>
</html>
```